Kelvaro.ch is looking for business card letterhead and envelope C5 with WOW effect

We need a strong business card for our company Kelvaro.ch, logo is available. You want a black or dark background on which the logo Stark r% 26 # 252; appears. Letterhead and envelope in C5 format should be in a similar design, but does not have to be We need a strong business card for our company Kelvaro.ch, logo is available. A black or dark background is desired, on which the logo Stark comes across. The letterhead and the envelope in C5 format should have a similar design.

Target Market(s)

Private customers as well as entrepreneurs

Contact Information for Business Card

E-mail: info@kelvaro-example.ch
Web.www.Kelvaro-example.ch
Tel: +41 ( 0 ) 79 482 6037
Adresse:
Lindenweg 14
9406 Tarnbach

Hier kann man Icons verwenden für Email,Tel und Adressse

Font styles to use
Other font styles liked:
• Dubai,bold

Colors

Designer to choose colors to be used in the design.

Requirements
Must have
• WOW effect
Nice to have
• R% 26 # 252; back business card with our service listings. - VEHICLE LABELING - SHOP WINDOW LABELING - STICKERS AND MUCH MORE ... in red color

```html
<!DOCTYPE html>
<html lang="en">
<head>
<meta charset="utf-8">
<title>Kelvaro.ch – Business Card</title>
<link rel="stylesheet" href="https://fonts.googleapis.com/css2?family=Montserrat:wght@400;500;700&display=swap">
<style>
  :root {
    --page-bg: #2b2c2e;
    --card-bg: #1b1c1e;
    --accent: #f8c517;
    --text-light: #f2f2f2;
    --text-silver: #b9bbbe;
    --rule: #6a6b6e;
  }
  * { box-sizing: border-box; margin: 0; padding: 0; }
  html, body { width: 1200px; height: 874px; overflow: hidden; }
  body {
    background: var(--page-bg);
    font-family: "Montserrat", sans-serif;
    position: relative;
  }
  .card {
    position: absolute;
    left: 260px;
    width: 680px;
    height: 388px;
    background: var(--card-bg);
    overflow: hidden;
    box-shadow: 0 10px 30px rgba(0,0,0,.45);
  }
  .card--front { top: 36px; }
  .card--back { top: 450px; }

  /* Front */
  .front-art {
    position: absolute;
    left: 0; top: 0;
    width: 340px; height: 388px;
    background: linear-gradient(120deg, #f8c517 0%, #e2b112 45%, #3a3320 80%, var(--card-bg) 100%);
  }
  .front-wordmark {
    position: absolute;
    right: 48px; top: 96px;
    font-size: 34px;
    font-weight: 700;
    letter-spacing: 1px;
    color: var(--text-silver);
    text-transform: uppercase;
    white-space: nowrap;
  }
  .service-list {
    position: absolute;
    right: 48px; top: 166px;
    list-style: none;
    text-align: right;
  }
  .service-list li {
    font-size: 14px;
    font-weight: 500;
    letter-spacing: .5px;
    color: var(--text-light);
    line-height: 24px;
    white-space: nowrap;
  }
  .service-list li::after {
    content: "";
    display: inline-block;
    width: 6px; height: 6px;
    border-radius: 50%;
    background: var(--accent);
    margin-left: 10px;
    vertical-align: middle;
  }

  /* Back */
  .back-texture {
    position: absolute;
    inset: 0;
    background: radial-gradient(ellipse at 65% 45%, rgba(248,197,23,.10) 0%, rgba(248,197,23,0) 65%);
  }
  .back-brand {
    position: absolute;
    right: 56px; top: 140px;
    display: flex;
    align-items: center;
    gap: 14px;
  }
  .back-brand__square {
    width: 52px; height: 52px;
    background: var(--accent);
  }
  .back-brand__name {
    font-size: 30px;
    font-weight: 700;
    color: var(--text-light);
    text-transform: uppercase;
    white-space: nowrap;
  }
  .contact {
    position: absolute;
    left: 48px; top: 108px;
  }
  .contact__name {
    font-size: 26px;
    font-weight: 700;
    color: var(--accent);
  }
  .contact__role {
    font-size: 15px;
    font-weight: 500;
    color: var(--text-light);
    margin-top: 2px;
  }
  .contact__list {
    list-style: none;
    margin-top: 22px;
  }
  .contact__list li {
    display: flex;
    align-items: center;
    gap: 10px;
    font-size: 14px;
    color: var(--text-light);
    line-height: 28px;
    white-space: nowrap;
  }
  .contact__list svg { width: 14px; height: 14px; flex: none; }
  .contact__row { display: flex; gap: 28px; }
  .contact__row span { display: flex; align-items: center; gap: 10px; }
  .back-rule {
    position: absolute;
    left: 48px; right: 48px; bottom: 42px;
    height: 1px;
    background: var(--rule);
  }
</style>
</head>
<body>

  <section class="card card--front">
    <div class="front-art" role="img" aria-label="Large yellow hexagon cluster graphic"></div>
    <div class="front-wordmark">Kelvaro.ch</div>
    <ul class="service-list">
      <li>VEHICLE LABELING</li>
      <li>SHOP WINDOW LABELING</li>
      <li>STICKERS</li>
    </ul>
  </section>

  <section class="card card--back">
    <div class="back-texture" role="img" aria-label="Faint golden network line pattern"></div>

    <div class="contact">
      <div class="contact__name">Lukas Hadorn</div>
      <div class="contact__role">President</div>
      <ul class="contact__list">
        <li>
          <svg viewBox="0 0 16 16" aria-hidden="true"><path fill="#f8c517" d="M3 1h3l1.5 4-2 1.3a9 9 0 0 0 4.2 4.2L11 8.5l4 1.5v3a2 2 0 0 1-2 2C6.4 15 1 9.6 1 3a2 2 0 0 1 2-2z"/></svg>
          +41 ( 0 ) 79 482 6037
        </li>
        <li>
          <svg viewBox="0 0 16 16" aria-hidden="true"><path fill="#f8c517" d="M8 0a5.5 5.5 0 0 0-5.5 5.5C2.5 10 8 16 8 16s5.5-6 5.5-10.5A5.5 5.5 0 0 0 8 0zm0 8a2.5 2.5 0 1 1 0-5 2.5 2.5 0 0 1 0 5z"/></svg>
          Lindenweg 14 9406 Tarnbach
        </li>
        <li class="contact__row">
          <span>
            <svg viewBox="0 0 16 16" aria-hidden="true"><path fill="#f8c517" d="M1 3h14v10H1z"/><path fill="none" stroke="#1b1c1e" stroke-width="1.4" d="M1.5 3.5 8 9l6.5-5.5"/></svg>
            info@kelvaro-example.ch
          </span>
          <span>
            <svg viewBox="0 0 16 16" aria-hidden="true"><circle cx="8" cy="8" r="7" fill="#f8c517"/><path fill="none" stroke="#1b1c1e" stroke-width="1.2" d="M1 8h14M8 1c-3 4-3 10 0 14M8 1c3 4 3 10 0 14"/></svg>
            www.Kelvaro-example.ch
          </span>
        </li>
      </ul>
    </div>

    <div class="back-brand">
      <div class="back-brand__square"></div>
      <div class="back-brand__name">Kelvaro.ch</div>
    </div>

    <div class="back-rule"></div>
  </section>

</body>
</html>
```